Business Card for Industrial Distributor

We need a business card design for an industrial distributor. We sell machine parts for the manufacturing and oil industry. We would like the cards to look clean and modern but with a touch of industry.

Our colors are blue/white.

Please feel free to visit our website www.korvelpartsco.com

Target Market(s)

mexican manufacturers in the automobile/aerospace industry

Industry/Entity Type

Industrial

Colors
ffffff
0555a3

```html
<!DOCTYPE html>
<html lang="en">
<head>
<meta charset="utf-8">
<title>Korvel Business Card</title>
<link href="https://fonts.googleapis.com/css2?family=Montserrat:wght@400;500;600;800&display=swap" rel="stylesheet">
<style>
  :root {
    --bg: #d9dbe0;
    --card-black: #050505;
    --brand-blue: #2f3fa8;
    --band-blue: #2a3a9c;
    --accent-blue: #1b8fe0;
    --orb-blue: #1f5fc4;
    --white: #ffffff;
  }
  * { margin: 0; padding: 0; box-sizing: border-box; }
  html, body { width: 1200px; height: 900px; overflow: hidden; }
  body {
    background: var(--bg);
    font-family: "Montserrat", sans-serif;
    position: relative;
  }
  .card {
    position: absolute;
    left: 270px;
    width: 660px;
    height: 377px;
    border-radius: 22px;
    background: var(--card-black);
    overflow: hidden;
  }
  .card--front { top: 50px; }
  .card--back { top: 473px; }

  /* Front */
  .front-brand {
    position: absolute;
    top: 120px;
    left: 0; right: 0;
    display: flex;
    align-items: center;
    justify-content: center;
    gap: 18px;
  }
  .brand-dot {
    width: 74px; height: 74px;
    border-radius: 50%;
    background: var(--orb-blue);
  }
  .brand-name {
    font-weight: 800;
    color: var(--brand-blue);
    letter-spacing: 1px;
    line-height: 1;
    white-space: nowrap;
  }
  .front-brand .brand-name { font-size: 92px; }
  .front-web {
    position: absolute;
    top: 282px;
    left: 0; right: 0;
    text-align: center;
    font-size: 19px;
    color: var(--accent-blue);
    letter-spacing: 0.5px;
  }
  .front-web strong { color: var(--white); font-weight: 600; }

  /* Back */
  .band {
    position: absolute;
    left: 0; right: 0;
    top: 218px; bottom: 0;
    background: var(--band-blue);
  }
  .back-name {
    position: absolute;
    top: 26px;
    left: 30px;
    font-size: 118px;
  }
  .back-orb {
    position: absolute;
    right: 26px;
    top: 100px;
    width: 160px; height: 160px;
    border-radius: 50%;
    background: var(--orb-blue);
  }
  .person {
    position: absolute;
    left: 36px;
    top: 160px;
  }
  .person-name {
    font-size: 25px;
    font-weight: 600;
    color: var(--accent-blue);
  }
  .person-title {
    font-size: 15px;
    color: var(--white);
    margin-top: 2px;
  }
  .contact {
    position: absolute;
    left: 60px;
    top: 240px;
    color: var(--white);
    font-size: 16px;
    line-height: 21px;
    list-style: none;
  }
  .contact .address { display: block; margin-bottom: 6px; }
  .contact li { display: flex; align-items: center; gap: 10px; }
  .contact svg { width: 13px; height: 13px; flex: none; fill: var(--white); }
  .contact strong { font-weight: 600; }
</style>
</head>
<body>

<section class="card card--front">
  <div class="front-brand">
    <span class="brand-dot"></span>
    <span class="brand-name">Korvel</span>
  </div>
  <p class="front-web">www.<strong>korvelpartsco</strong>.com</p>
</section>

<section class="card card--back">
  <div class="band"></div>
  <span class="brand-name back-name">Korvel</span>
  <span class="back-orb"></span>
  <div class="person">
    <p class="person-name">Marek Lindqvist</p>
    <p class="person-title">Director</p>
  </div>
  <ul class="contact">
    <li class="address">P.O. Box 4410<br>Lakeview, MI 49888</li>
    <li>
      <svg viewBox="0 0 16 16"><path d="M3.6 1.5l2.3 2.7-1.3 1.8c.9 2 2.4 3.5 4.4 4.4l1.8-1.3 2.7 2.3-1.3 2.6C7 13.8 2.2 9 1 3z"/></svg>
      <span>+330 2480-1193</span>
    </li>
    <li>
      <svg viewBox="0 0 16 16"><path d="M1 3h14v10H1z M2.5 4.5v.3L8 8.6l5.5-3.8v-.3z" fill-rule="evenodd"/></svg>
      <span>info@korvelpartsco.com</span>
    </li>
    <li>
      <svg viewBox="0 0 16 16"><circle cx="8" cy="8" r="7"/><path d="M1 8h14M8 1c-3 3.5-3 10.5 0 14M8 1c3 3.5 3 10.5 0 14" stroke="#2a3a9c" stroke-width="1.2" fill="none"/></svg>
      <span>www.<strong>korvelpartsco</strong>.com</span>
    </li>
  </ul>
</section>

</body>
</html>
```